Heritage Hollow Business Cards

Require a business card design. <br/><br/>Needs to include logo (either round or long version) plus these details:<br/>Maya Torvell<br/>Heritage Hollow<br/>maya@kelvadtrading.com.au<br/>02 6481 7395<br/>PO Box Glenwarra NSW 2791<br/>www.heritagehollow.com.au<br/><br/>I need in an editable format so that I can create for multiple staff members. <br/><br/>

Target Market(s)

We are an online store selling renovation products to home owners are builders. Looking for a classic classy design.

Industry/Entity Type

Home And Garden

Contact Information for Business Card

Maya Torvell
Heritage Hollow
maya@kelvadtrading.com.au
02 6481 7395
PO Box Glenwarra NSW 2791
www.heritagehollow.com.au

Colors

Designer to choose colors to be used in the design.

Requirements
Must have
• Must include Logo.

```html
<!DOCTYPE html>
<html lang="en">
<head>
<meta charset="utf-8">
<title>Heritage Hollow Business Cards</title>
<link href="https://fonts.googleapis.com/css2?family=Montserrat:wght@400;600&display=swap" rel="stylesheet">
<style>
  :root {
    --backdrop: #2a2a2a;
    --card-black: #070707;
    --card-white: #ffffff;
    --sage: #57705f;
    --ink: #262626;
    --paper-text: #f2f2f2;
    --faint-line: #3a3a3a;
  }
  * { margin: 0; padding: 0; box-sizing: border-box; }
  html, body {
    width: 1200px; height: 900px; overflow: hidden;
    background: var(--backdrop);
    font-family: "Montserrat", sans-serif;
  }
  .canvas {
    width: 1200px; height: 900px;
    display: flex; flex-direction: column; align-items: center; justify-content: center;
    gap: 40px;
  }
  .card {
    position: relative; width: 700px; height: 389px; overflow: hidden;
    box-shadow: 0 12px 30px rgba(0,0,0,.45);
  }

  /* Front */
  .card-front { background: var(--card-black); }
  .roof-artwork {
    position: absolute; left: 30px; top: 40px; width: 640px; height: 290px;
    background: radial-gradient(ellipse at 55% 45%, #1b1b1b 0%, #0f0f0f 55%, rgba(7,7,7,0) 80%);
  }
  .front-emblem {
    position: absolute; left: 252px; top: 78px; width: 230px; height: 230px;
    border: 1.5px solid var(--paper-text); border-radius: 50%;
    display: flex; align-items: center; justify-content: center; text-align: center;
  }
  .front-emblem .brand-name {
    color: var(--paper-text); font-weight: 600; font-size: 28px; line-height: 1.1;
  }

  /* Back */
  .card-back { background: var(--card-white); }
  .band {
    position: absolute; left: 0; right: 0; top: 92px; height: 150px;
    background: var(--sage);
  }
  .back-emblem {
    position: absolute; left: 22px; top: 56px; width: 212px; height: 212px;
    background: var(--card-white); border-radius: 50%;
    display: flex; align-items: center; justify-content: center;
  }
  .back-emblem .ring {
    width: 160px; height: 160px; border: 1px solid var(--ink); border-radius: 50%;
    display: flex; align-items: center; justify-content: center; text-align: center;
  }
  .back-emblem .brand-name {
    color: var(--ink); font-weight: 600; font-size: 21px; line-height: 1.1;
  }
  .contact {
    position: absolute; right: 58px; top: 118px; text-align: right; color: var(--ink);
  }
  .contact .person-name {
    font-weight: 600; font-size: 29px; letter-spacing: .5px; margin-bottom: 8px;
  }
  .contact .line {
    display: flex; align-items: center; justify-content: flex-end; gap: 8px;
    font-size: 15px; line-height: 22px; color: var(--paper-text);
  }
  .contact .line svg { width: 15px; height: 15px; flex: none; }
  .address {
    position: absolute; left: 248px; top: 318px;
    font-size: 17px; color: var(--ink); letter-spacing: .3px;
  }
</style>
</head>
<body>
<main class="canvas">
  <section class="card card-front">
    <div class="roof-artwork" role="img" aria-label="Faint sketched roofline illustration"></div>
    <div class="front-emblem">
      <span class="brand-name">Heritage<br>Hollow</span>
    </div>
  </section>

  <section class="card card-back">
    <div class="band"></div>
    <div class="back-emblem">
      <div class="ring"><span class="brand-name">Heritage<br>Hollow</span></div>
    </div>
    <div class="contact">
      <p class="person-name">Maya Torvell</p>
      <p class="line">02 6481 7395
        <svg viewBox="0 0 16 16" aria-hidden="true"><path d="M4 1.5l2.2 3-1.3 1.6c.8 1.8 2.2 3.2 4 4l1.6-1.3 3 2.2-1.2 2.5C7.5 13.3 2.7 8.5 1.5 3.7z" fill="none" stroke="currentColor" stroke-width="1.3" stroke-linejoin="round"/></svg>
      </p>
      <p class="line">maya@kelvadtrading.com.au
        <svg viewBox="0 0 16 16" aria-hidden="true"><rect x="1.5" y="3.5" width="13" height="9" fill="none" stroke="currentColor" stroke-width="1.3"/><path d="M1.5 3.5L8 9l6.5-5.5" fill="none" stroke="currentColor" stroke-width="1.3"/></svg>
      </p>
      <p class="line">www.heritagehollow.com.au
        <svg viewBox="0 0 16 16" aria-hidden="true"><circle cx="8" cy="8" r="6.5" fill="none" stroke="currentColor" stroke-width="1.3"/><ellipse cx="8" cy="8" rx="2.8" ry="6.5" fill="none" stroke="currentColor" stroke-width="1.1"/><path d="M1.5 8h13M2.5 5h11M2.5 11h11" stroke="currentColor" stroke-width="1"/></svg>
      </p>
    </div>
    <p class="address">PO Box Glenwarra NSW 2791</p>
  </section>
</main>
</body>
</html>
```